VOMRA Pty Ltd Business Card

Looking for a simple yet eye-catching double-sided business card design using my company logo on one side and contact details on the other.

Target Market(s)

Government

Industry/Entity Type

Communication Systems Engineering

Contact Information for Business Card

VOMRA Pty Ltd

Requirements
Nice to have
• Would be great to have a QR code so details can be scanned into contacts

```html
<!DOCTYPE html>
<html lang="en">
<head>
<meta charset="utf-8">
<title>VOMRA Pty Ltd Business Card</title>
<link href="https://fonts.googleapis.com/css2?family=Open+Sans:wght@400;600;700&display=swap" rel="stylesheet">
<style>
  :root {
    --page: #e9e6e2;
    --slate: #37414a;
    --slate-deep: #2b333a;
    --ink: #2f3a44;
    --paper: #ffffff;
  }
  * { box-sizing: border-box; margin: 0; padding: 0; }
  html, body { width: 1200px; height: 780px; overflow: hidden; }
  body {
    background: var(--page);
    font-family: "Open Sans", sans-serif;
    color: var(--ink);
    position: relative;
  }
  .card {
    position: absolute;
    top: 70px;
    width: 366px;
    height: 640px;
    border-radius: 26px;
    box-shadow: 0 10px 28px rgba(0,0,0,0.22);
    overflow: hidden;
  }
  /* Logo side */
  .card-back { left: 190px; background: var(--slate); }
  .back-wordmark {
    position: absolute;
    left: 50%; top: 36%;
    transform: translate(-50%, -50%) rotate(90deg);
    font-size: 76px;
    font-weight: 700;
    letter-spacing: 8px;
    padding-left: 8px;
    line-height: 1;
    white-space: nowrap;
    color: var(--slate-deep);
  }
  .back-mark {
    position: absolute;
    left: 50%; top: 80%;
    width: 110px; height: 110px;
    transform: translate(-50%, -50%);
    border-radius: 50%;
    background: var(--slate-deep);
  }
  /* Contact side */
  .card-front { left: 646px; background: var(--paper); padding: 40px 30px 0 30px; }
  .brand { display: flex; align-items: center; gap: 16px; }
  .brand-dot { width: 62px; height: 62px; border-radius: 50%; background: var(--ink); }
  .brand-name { font-size: 46px; font-weight: 700; letter-spacing: 4px; color: var(--ink); }
  .person { margin-top: 200px; text-align: center; }
  .person-name { font-size: 38px; font-weight: 700; line-height: 1.05; }
  .person-role { font-size: 17px; font-weight: 600; margin-top: 2px; }
  .dot-row { display: block; width: 100%; height: 20px; margin: 6px 0; }
  .contact-lines { text-align: center; font-size: 17px; line-height: 1.35; }
  .address { text-align: center; font-size: 17px; line-height: 1.35; margin-top: 4px; }
</style>
</head>
<body>

<section class="card card-back" aria-label="Card back">
  <div class="back-wordmark">VOMRA</div>
  <div class="back-mark"></div>
</section>

<section class="card card-front" aria-label="Card front">
  <div class="brand">
    <div class="brand-dot"></div>
    <div class="brand-name">VOMRA</div>
  </div>

  <div class="person">
    <div class="person-name">Jordan Hale</div>
    <div class="person-role">Co-Founder</div>
  </div>

  <svg class="dot-row" viewBox="0 0 306 20" aria-hidden="true">
    <g fill="var(--ink)">
      <circle cx="6" cy="10" r="2.5"/><circle cx="22" cy="10" r="3.5"/><circle cx="40" cy="10" r="4.5"/><circle cx="60" cy="10" r="5.5"/><circle cx="82" cy="10" r="6.5"/>
      <circle cx="224" cy="10" r="6.5"/><circle cx="246" cy="10" r="5.5"/><circle cx="266" cy="10" r="4.5"/><circle cx="284" cy="10" r="3.5"/><circle cx="300" cy="10" r="2.5"/>
      <circle cx="113" cy="10" r="10"/><circle cx="153" cy="10" r="10"/><circle cx="193" cy="10" r="10"/>
    </g>
    <g fill="none" stroke="#fff" stroke-width="1.4" stroke-linecap="round">
      <path d="M109 5 q-2 5 3 9 q4 2 5 0 l-2-2 -2 1 q-2-2-2-4 l1-1 -1-3z" fill="#fff" stroke="none"/>
      <rect x="147" y="6" width="12" height="8" rx="1"/><path d="M147 6 l6 5 6-5"/>
      <circle cx="193" cy="10" r="6"/><path d="M187 10 h12 M193 4 q-4 6 0 12 M193 4 q4 6 0 12"/>
    </g>
  </svg>

  <div class="contact-lines">
    <div>(555) 014-2207</div>
    <div>www.vomra.com.au</div>
    <div>admin@vomra.com.au</div>
  </div>

  <svg class="dot-row" viewBox="0 0 306 20" aria-hidden="true">
    <g fill="var(--ink)">
      <circle cx="6" cy="10" r="2.5"/><circle cx="22" cy="10" r="3.5"/><circle cx="40" cy="10" r="4.5"/><circle cx="60" cy="10" r="5.5"/><circle cx="82" cy="10" r="6.5"/><circle cx="106" cy="10" r="7"/><circle cx="130" cy="10" r="7"/>
      <circle cx="176" cy="10" r="7"/><circle cx="200" cy="10" r="7"/><circle cx="224" cy="10" r="6.5"/><circle cx="246" cy="10" r="5.5"/><circle cx="266" cy="10" r="4.5"/><circle cx="284" cy="10" r="3.5"/><circle cx="300" cy="10" r="2.5"/>
      <circle cx="153" cy="10" r="10"/>
    </g>
    <path d="M153 16 q-5-5-5-8 a5 5 0 0 1 10 0 q0 3-5 8z" fill="#fff"/>
    <circle cx="153" cy="8" r="1.8" fill="var(--ink)"/>
  </svg>

  <div class="address">
    <div>42-44 Harbour Lane Westfield</div>
    <div>NSW 2150 Australia</div>
  </div>
</section>

</body>
</html>
```